Natural Organic soap need packaging design

we need a packaging design for new company based in New Zealand Called 'Tessmar International ltd'.. We manufacture Natural organic soap bars.our main USP is that this soap is made of all natural ingredient and no chemical used and soap is made in New Zealand,so we need a design which look natural,simple,classy and luxury and packaging should reflect that its made in New Zealand.please find attached photos of sample soap.
soap will be in two variant:
1. Pure Manuka Honey soap
2. Goat Milk soap
NOTE: the soap in picture is not actually our soap its just a sample what our soap will look like so please don't make a design with KLOPPE written on it. TESSMAR is the soap name.
Target Market(s)
international market. mainly young and kids
Industry/Entity Type
It Company
Look and feel
Each slider illustrates characteristics of the customer's brand and the style your logo design should communicate.

```html
<!DOCTYPE html>
<html lang="en">
<head>
<meta charset="utf-8">
<title>Tessmar – Pure Manuka Honey Soap</title>
<link rel="stylesheet" href="https://fonts.googleapis.com/css2?family=Exo+2:wght@300;600&display=swap">
<style>
  :root {
    --backdrop: #e2e2e2;
    --honey: #e6a714;
    --honey-deep: #cf930c;
    --cream: #fdf7e6;
  }
  * { margin: 0; padding: 0; box-sizing: border-box; }
  html, body {
    width: 1200px;
    height: 801px;
    overflow: hidden;
    background: var(--backdrop);
  }
  .canvas {
    position: relative;
    width: 1200px;
    height: 801px;
  }
  .box-front {
    position: absolute;
    left: 410px;
    top: 150px;
    width: 380px;
    height: 500px;
    background: var(--honey);
    color: var(--cream);
    font-family: "Exo 2", sans-serif;
  }
  .frame {
    position: absolute;
    inset: 0;
  }
  .honeycomb {
    position: absolute;
    left: 80px;
    top: 215px;
    width: 170px;
    height: 240px;
    border-radius: 40%;
    background: radial-gradient(ellipse at center, var(--honey-deep) 0%, rgba(207,147,12,0.6) 55%, rgba(230,167,20,0) 75%);
  }
  .label {
    position: absolute;
    left: 50%;
    top: 50%;
    width: 500px;
    height: 380px;
    transform: translate(-50%, -50%) rotate(-90deg);
    display: flex;
    flex-direction: column;
    align-items: center;
    justify-content: center;
  }
  .product-name {
    font-weight: 300;
    font-size: 27px;
    letter-spacing: 0.5px;
    margin-bottom: 10px;
  }
  .brand-name {
    font-weight: 600;
    font-size: 78px;
    line-height: 1;
    letter-spacing: 2px;
  }
  .origin {
    margin-top: 16px;
    font-weight: 300;
    font-size: 14px;
    letter-spacing: 11px;
    padding-left: 11px;
  }
</style>
</head>
<body>
  <main class="canvas">
    <section class="box-front">
      <svg class="frame" viewBox="0 0 380 500" width="380" height="500" aria-hidden="true">
        <path d="M32 14 H348 A18 18 0 0 0 366 32 V468 A18 18 0 0 0 348 486 H32 A18 18 0 0 0 14 468 V32 A18 18 0 0 0 32 14 Z"
              fill="none" stroke="var(--cream)" stroke-width="2.5"/>
        <path d="M34 22 H346 A12 12 0 0 0 358 34 V466 A12 12 0 0 0 346 478 H34 A12 12 0 0 0 22 466 V34 A12 12 0 0 0 34 22 Z"
              fill="none" stroke="var(--cream)" stroke-width="1"/>
      </svg>
      <div class="honeycomb" role="img" aria-label="Faint honeycomb pattern"></div>
      <div class="label">
        <p class="product-name">Pure Manuka Honey Soap</p>
        <h1 class="brand-name">TESSMAR</h1>
        <p class="origin">NEW ZEALAND</p>
      </div>
    </section>
  </main>
</body>
</html>
```